Bold Harbor Web Design Layout (no HTML)

We require the layout only for a website.  No html or logo is required - just the layout.

A refreshed and revitalized website to coincide with the relaunch of our brand. We are looking for a clean simplistic design that is easy to use and presents relevant information effectively.
We are an events management company specializing in conferences.
Updates

Thank you for your design. We really like the imagery. Essentially we are after a home page design (one page) that incorporates the 3 main buttons (request a proposal, select a venue and specials) while providing the relevant information on our service via functionality similar to that on www.plivtrak.com ie using the large arrow to scroll over the relevant topic to receive information. We hope to finalise the contest in the next week and hope to consider your revised entry.

Thanks!

Target Market(s)

Australian corporate sector primarily Managing Directors or their assistants. Any business looking to hold a conference for up 500 delegates however we are primarily targeting the decision maker so need to ensure we are communicating on their terms.

Industry/Entity Type

Event

Requirements
Must have
• Incorporate the elements from the attached document however with complete creative license as to their layout. Our main competitors are gathorly.com.au, talkhollowhq.com.au both sites are bland and not user friendly.
Nice to have
• Colours red, silver and black. Note we are running a separate contest to refresh our logo.
• We like the functionality of plivtrak.com

```html
<!DOCTYPE html>
<html lang="en">
<head>
<meta charset="utf-8">
<title>Bold Harbor – Conference Management</title>
<link rel="stylesheet" href="https://fonts.googleapis.com/css2?family=Questrial&family=Arimo:wght@400;700&display=swap">
<style>
:root{
  --black:#000;
  --white:#fff;
  --red:#e30000;
  --red-dark:#a80000;
  --red-deep:#c00000;
  --grey-panel:#e6e6e6;
  --grey-text:#6a6a6a;
  --ink:#111;
  --charcoal:#2b2b2b;
}
*{box-sizing:border-box;margin:0;padding:0}
html,body{width:1200px;height:684px;overflow:hidden;background:var(--black)}
body{position:relative;font-family:"Questrial",sans-serif;color:var(--ink)}
.band{position:absolute;left:0;top:97px;width:1200px;height:41px;background:var(--white)}
.page{position:absolute;left:157px;top:9px;width:882px;height:622px;background:var(--white);border-radius:8px}
.abs{position:absolute}
.header{left:165px;top:16px;width:866px;height:82px;border-radius:6px 6px 0 0;
  background:radial-gradient(ellipse at 55% 50%,#ff1a1a 0%,#d80000 30%,#5a0000 62%,#1a0000 85%),#200;
  }
.header::after{content:"";position:absolute;inset:0;border-radius:inherit;
  background:repeating-linear-gradient(135deg,rgba(0,0,0,.18) 0 2px,transparent 2px 5px)}
.logo-text{left:204px;top:56px;font-family:"Arimo",sans-serif;font-size:11px;color:var(--white);z-index:2}
.search-label{left:753px;top:68px;font-family:"Arimo",sans-serif;font-weight:700;font-size:14px;color:var(--white);z-index:2}
.search-input{left:814px;top:67px;width:178px;height:19px;background:var(--white);border:1px solid #999;z-index:2}
.search-go{left:994px;top:64px;width:27px;height:27px;border-radius:4px;background:linear-gradient(#e04040,#900);border:1px solid #fff;
  color:var(--white);font-family:"Arimo",sans-serif;font-weight:700;font-size:12px;line-height:25px;text-align:center;z-index:2}
.nav{left:165px;top:97px;width:866px;height:41px;background:var(--black)}
.nav ul{list-style:none;display:flex;gap:11px;position:absolute;left:71px;top:19px}
.nav li{color:var(--white);font-size:14px;letter-spacing:-.2px}
.nav li.current{color:#dde6ff;font-weight:700;position:relative}
.nav li.current::after{content:"";position:absolute;left:16px;top:19px;border:5px solid transparent;border-bottom-color:var(--white)}
.side-menu{left:165px;top:194px;width:137px}
.side-menu a{display:block;height:28px;line-height:28px;padding-left:20px;font-size:14px;color:var(--ink);text-decoration:none}
.side-menu a.active{height:31px;line-height:31px;margin-bottom:12px;color:var(--white);
  background:linear-gradient(var(--red),var(--red-deep));clip-path:polygon(0 0,92% 0,100% 50%,92% 100%,0 100%);}
.divider{width:1px;background:linear-gradient(#fff,#ccc 20%,#ccc 80%,#fff)}
.intro{left:328px;top:161px;width:480px;font-size:16.5px;line-height:19.5px;color:var(--ink)}
.intro strong{font-weight:700;font-family:"Arimo",sans-serif;font-size:16px}
.finance{left:313px;top:239px;width:495px;height:237px;background:var(--grey-panel);border-radius:8px}
.finance h2{position:absolute;left:33px;top:10px;font-size:16px;font-weight:700;color:#555;font-family:"Arimo",sans-serif;letter-spacing:-.2px}
.finance .art{position:absolute;left:24px;top:59px;width:113px;height:152px;border-radius:40px;
  background:radial-gradient(circle at 55% 40%,#ff3a1a,#b00000 70%,transparent 72%)}
.finance ul{position:absolute;left:163px;top:43px;list-style:none;font-size:14.5px;line-height:15.8px;color:var(--grey-text)}
.finance li::before{content:"•";margin-right:8px}
.finance p{position:absolute;left:148px;top:170px;width:335px;font-size:14.5px;line-height:16px;color:var(--grey-text)}
.goals{left:816px;top:155px;width:202px;height:325px;border-radius:7px;background:linear-gradient(90deg,var(--red-deep),var(--red) 40%,var(--red-dark))}
.goals h3{position:absolute;left:5px;top:34px;font-size:17.5px;font-weight:400;line-height:20px;color:var(--white)}
.goals ul{list-style:none}
.goals li{position:absolute;left:11px;font-size:19.5px;line-height:21px;color:var(--white)}
.arrow{left:760px;top:261px;width:253px;height:61px;z-index:3}
.arrow span{position:absolute;left:67px;top:16px;font-size:20px;color:var(--white)}
.tab{height:18px;padding-left:9px;font-family:"Arimo",sans-serif;font-size:12px;line-height:18px;color:var(--white);
  background:linear-gradient(#ff2020,var(--red-deep));border-radius:0 5px 0 0}
.teaser{font-family:"Arimo",sans-serif;font-size:11.2px;line-height:12.3px;width:110px;color:var(--ink)}
.icon-art{width:72px;height:72px}
.footer{left:165px;top:598px;width:866px;height:24px;background:var(--black);border-radius:0 0 4px 4px;
  font-family:"Arimo",sans-serif;font-size:9.5px;color:var(--white);text-align:center;line-height:24px}
</style>
</head>
<body>
<div class="band"></div>
<div class="page"></div>

<header>
  <div class="abs header"></div>
  <div class="abs logo-text">LOGO GOES HERE</div>
  <div class="abs search-label">SEARCH:</div>
  <div class="abs search-input"></div>
  <div class="abs search-go">GO</div>
</header>

<nav class="abs nav">
  <ul>
    <li class="current">HOME</li><li>SERVICES</li><li>VENUES</li><li>CLIENTS</li><li>REGISTER</li><li>CONTACT US</li>
  </ul>
</nav>

<aside class="abs side-menu">
  <a class="active" href="#">OTHER MENU</a>
  <a href="#">OTHER MENU</a>
  <a href="#">OTHER MENU</a>
  <a href="#">OTHER MENU</a>
  <a href="#">OTHER MENU</a>
  <a href="#">OTHER MENU</a>
</aside>
<div class="abs divider" style="left:302px;top:155px;height:440px"></div>

<p class="abs intro"><strong>Bold Harbor</strong>' professional conference team specialises in solutions. We work closely with a core group of clients to ensure desired outcomes, on time and in budget.</p>

<section class="abs finance">
  <h2>We offer a complete range of finance&nbsp; packages including;</h2>
  <div class="art" role="img" aria-label="Red 3D dollar sign illustration"></div>
  <ul>
    <li>total conference underwriting</li>
    <li>online delegate payment gateway</li>
    <li>substantially discounted rooming rates</li>
    <li>no upfront costs</li>
    <li>zero management fees</li>
    <li>free venue sourcing</li>
    <li>free delegate booking management</li>
  </ul>
  <p>Minimise your costs and free your cash flow to focus on your core business functions. We'll ensure maximum return from your conference budget.</p>
</section>

<section class="abs goals">
  <h3>Our goal is to make<br>sure your conference is:</h3>
  <ul>
    <li style="top:198px">Expertely Managed<br>&amp; Hassle Free</li>
    <li style="top:262px">Outcome Focussed</li>
    <li style="top:306px">Well Attended</li>
  </ul>
</section>
<div class="abs arrow">
  <svg width="253" height="61" viewBox="0 0 253 61">
    <defs><linearGradient id="arrowFill" x1="0" y1="0" x2="0" y2="1"><stop offset="0" stop-color="#5a5a5a"/><stop offset=".5" stop-color="#333"/><stop offset="1" stop-color="#1c1c1c"/></linearGradient></defs>
    <path d="M30 2H247a4 4 0 0 1 4 4V55a4 4 0 0 1-4 4H30L2 30.5Z" fill="url(#arrowFill)" stroke="#fff" stroke-width="3"/>
  </svg>
  <span>Cost Effective</span>
</div>

<div class="abs divider" style="left:539px;top:484px;height:110px"></div>
<div class="abs divider" style="left:804px;top:484px;height:110px"></div>

<section>
  <div class="abs tab" style="left:313px;top:493px;width:200px">Special Offers</div>
  <p class="abs teaser" style="left:318px;top:512px">Not sure where to start? We have over 60 properties to choose from both domestically and international.</p>
  <div class="abs icon-art" role="img" aria-label="Red seal badge with dollar sign" style="left:441px;top:516px;border-radius:50%;background:radial-gradient(circle,#e01010,#900)"></div>

  <div class="abs tab" style="left:562px;top:493px;width:199px">Request Proposal</div>
  <p class="abs teaser" style="left:567px;top:512px">Not sure where to start? We have over 60 properties to choose from both domestically and international.</p>
  <div class="abs icon-art" role="img" aria-label="Wall clock illustration" style="left:697px;top:516px;border-radius:50%;background:radial-gradient(circle,#fafafa 55%,#c8c8c8 62%,#a00 66%,#700)"></div>

  <div class="abs tab" style="left:817px;top:493px;width:201px">Browse Conference</div>
  <p class="abs teaser" style="left:821px;top:512px">Not sure where to start? We have over 60 properties to choose from both domestically and international.</p>
  <div class="abs icon-art" role="img" aria-label="Red map of Australia illustration" style="left:933px;top:515px;border-radius:40%;background:radial-gradient(circle at 50% 45%,#ff3a1a,#b00000 70%,transparent 72%)"></div>
</section>

<footer class="abs footer">Ph: 1300 555 014. P.O. Box 2214, Eastwood Ridge NSW 2170. Bold Harbor. All Rights Reserved. 2009</footer>
</body>
</html>
```